verdant terraces simple classy business card design

my name is colin barrow and I run a gardening business aimed at high class verdant terraces. the business name is verdant terraces and our logo was designed on pixel harbour .My clientel are anything from residential homes to businesses. I take pride in my work and know that I offer a service like no other in my area.
The business card will be used to represent my business and I want it to be not only rememberable, but simplistic and modern. Eye catching too. Of course I would like it relatable to gardening and appealing to the correct clientel - those being garden enthusiasts, prestigious homes and businesses that are after top of the line gardening services like no other on the market.
I am not a typical lawn mowing business so I don't want a typical card design that represents that. The gardens I work with are generally million dollar properties with owners who are very garden proud looking for upkeep and guidance from me along with sometimes whole new garden designs. I want the business cards to show to my clients that I take pride, as they do, in their garden. And I want them to know from my card that I am a professional, qualified horticulturist offering them a top of the line service for life. I want them to refer my business on. I want them to look at my business card and see class and professionalism in a modern unique bold way.
The card should be simple with the possibility of the logo on the front being embossed/debossed and my details on the back the card should have a organic garden feel it's very important to me that it is absolutely perfect
I am also very open to ideas and suggestions so look forward to seeing the designs. the business logo has been supplied with this project and I want the card to be double sided

Contact info is
Colin Barrow - Managing Director / Horticulturist
Phone : 0481 526 704
Email: colinbarrow@verdantterraces.example.au

Target Market(s)

high class gardens residential and commercial

Industry/Entity Type

Gardener

Contact Information for Business Card

Contact info is
Phone : 0481 526 704

PLEASE MAKE CARD DOUBLE SIDED

Requirements
Must have
• organic simple classy modern feel
• must flow with the current logo that has been supplied with this project
• Double sided
• Must explain in a simple way that I deal with high end gardens and I'm a qualified horticulturist
Nice to have
• embossed debossed logo
Should not have
• shouldn't be to busy or cheap looking

```html
<!DOCTYPE html>
<html lang="en">
<head>
<meta charset="utf-8">
<title>Verdant Terraces – Business Card</title>
<link rel="stylesheet" href="https://fonts.googleapis.com/css2?family=Cinzel:wght@600&family=Open+Sans:wght@400;600;700&display=swap">
<style>
  :root {
    --leaf-green: #5aa845;
    --ink-grey: #3d3d3d;
    --divider-grey: #7a7a7a;
    --card-white: #f7f7f5;
    --backdrop: #e9e4dc;
  }
  * { margin: 0; padding: 0; box-sizing: border-box; }
  html, body {
    width: 1200px;
    height: 794px;
    overflow: hidden;
    background: var(--backdrop);
  }
  .canvas {
    position: relative;
    width: 1200px;
    height: 794px;
  }
  .card {
    position: absolute;
    width: 540px;
    height: 300px;
    background: var(--card-white);
    box-shadow: 0 6px 18px rgba(60, 50, 40, 0.18);
  }
  .card--details { left: 140px; top: 80px; }
  .card--brand   { left: 520px; top: 414px; }

  /* details side */
  .brand-mark {
    position: absolute;
    left: 58px;
    top: 74px;
    width: 150px;
    display: flex;
    flex-direction: column;
    align-items: center;
    gap: 12px;
  }
  .brand-mark__circle {
    width: 96px;
    height: 96px;
    border-radius: 50%;
    background: var(--leaf-green);
  }
  .brand-mark__name {
    font-family: "Open Sans", sans-serif;
    font-weight: 700;
    font-size: 13px;
    letter-spacing: 0.06em;
    color: var(--leaf-green);
    text-transform: uppercase;
    text-align: center;
  }
  .divider {
    position: absolute;
    left: 246px;
    top: 58px;
    width: 2px;
    height: 176px;
    background: var(--divider-grey);
  }
  .contact {
    position: absolute;
    left: 270px;
    top: 64px;
    font-family: "Open Sans", sans-serif;
    color: var(--ink-grey);
  }
  .contact__name {
    font-weight: 700;
    font-size: 19px;
    color: var(--leaf-green);
    letter-spacing: 0.02em;
    line-height: 1.15;
  }
  .contact__role {
    font-weight: 600;
    font-size: 13.5px;
    line-height: 1.3;
    text-transform: uppercase;
  }
  .contact__lines {
    margin-top: 18px;
    font-size: 13px;
    line-height: 1.45;
  }
  .contact__label { color: var(--leaf-green); font-weight: 600; }

  /* brand side */
  .wordmark {
    position: absolute;
    inset: 0;
    display: flex;
    flex-direction: column;
    align-items: center;
    justify-content: center;
    gap: 14px;
  }
  .wordmark__circle {
    width: 70px;
    height: 70px;
    border-radius: 50%;
    background: var(--leaf-green);
  }
  .wordmark__name {
    font-family: "Cinzel", serif;
    font-weight: 600;
    font-size: 38px;
    letter-spacing: 0.08em;
    color: var(--leaf-green);
  }
</style>
</head>
<body>
<main class="canvas">
  <section class="card card--details" aria-label="Business card, details side">
    <div class="brand-mark">
      <div class="brand-mark__circle"></div>
      <span class="brand-mark__name">Verdant Terraces</span>
    </div>
    <div class="divider"></div>
    <div class="contact">
      <p class="contact__name">COLIN BARROW</p>
      <p class="contact__role">Managing Director</p>
      <p class="contact__role">Horticulturist</p>
      <div class="contact__lines">
        <p><span class="contact__label">Phone</span> : 0481 526 704</p>
        <p>colinbarrow@verdantterraces.example.au</p>
        <p>www.verdantterraces.example.au</p>
      </div>
    </div>
  </section>

  <section class="card card--brand" aria-label="Business card, brand side">
    <div class="wordmark">
      <div class="wordmark__circle"></div>
      <span class="wordmark__name">VERDANT TERRACES</span>
    </div>
  </section>
</main>
</body>
</html>
```